Business Card Design Project

We need a business card for our new business based in Vancouver called
"Korvi" We are looking for a simple yet bold design for our business cards that will enable us to stand out from the pack. All business card details will be provided in the handover stage.
Updates

Thank you to all who have submitted

The work is great for the most part
Cards with creative use of the logo
have been more successful so far

Dark cards and rounded edges 
are also getting good reviews

Double sided is an option we would like to see explored

Thank you

Target Market(s)

Our clients are stressed business people, yoga/meditation enthusiast, and people looking for a new experience in a Spa enviroment

Industry/Entity Type

Business

Font styles to use
Other font styles liked:
• please check design file

Requirements
Must have
• Korvi

5217 E Halden Row, Vancouver, BC V5N 4K7

korvi@calmhaus.ca
Nice to have
• Creative approach to layout and design

Outside of the box design elements
Should not have
• Should not be too busy

```html
<!DOCTYPE html>
<html lang="en">
<head>
<meta charset="utf-8">
<title>Korvi — Business Card</title>
<link href="https://fonts.googleapis.com/css2?family=Arimo:wght@400&display=swap" rel="stylesheet">
<style>
  :root {
    --page-bg: #f7f5f2;
    --card-bg: #000000;
    --text-grey: #8a8a8a;
    --text-dim: #6f6f6f;
  }
  * { margin: 0; padding: 0; box-sizing: border-box; }
  html, body {
    width: 1200px;
    height: 849px;
    overflow: hidden;
    background: var(--page-bg);
    font-family: "Arimo", Arial, sans-serif;
  }
  .canvas {
    position: relative;
    width: 1200px;
    height: 849px;
  }
  .business-card {
    position: absolute;
    left: 272px;
    top: 224px;
    width: 648px;
    height: 391px;
    border-radius: 78px;
    background: var(--card-bg);
    text-align: center;
    color: var(--text-grey);
  }
  .brand {
    position: absolute;
    top: 44px;
    left: 0;
    width: 100%;
    display: flex;
    justify-content: center;
    align-items: center;
    gap: 16px;
  }
  .brand-dot {
    width: 34px;
    height: 34px;
    border-radius: 50%;
    border: 2px solid var(--text-grey);
  }
  .brand-name {
    font-size: 40px;
    letter-spacing: 5px;
    color: var(--text-grey);
    font-weight: 400;
  }
  .person-name {
    position: absolute;
    top: 150px;
    width: 100%;
    font-size: 22px;
    letter-spacing: 4px;
  }
  .person-title {
    position: absolute;
    top: 180px;
    width: 100%;
    font-size: 13px;
    letter-spacing: 2.4px;
  }
  .phone {
    position: absolute;
    top: 228px;
    width: 100%;
    font-size: 21px;
    letter-spacing: 3.6px;
  }
  .email {
    position: absolute;
    top: 260px;
    width: 100%;
    font-size: 17px;
    letter-spacing: 2px;
  }
  .address {
    position: absolute;
    top: 324px;
    width: 100%;
    font-size: 13px;
    letter-spacing: 1.6px;
    color: var(--text-dim);
    line-height: 19px;
  }
</style>
</head>
<body>
<div class="canvas">
  <div class="business-card">
    <div class="brand">
      <span class="brand-dot"></span>
      <span class="brand-name">Korvi</span>
    </div>
    <p class="person-name">Lorcan Wei Ashbury</p>
    <p class="person-title">Health Consultant</p>
    <p class="phone">+098 417 260934</p>
    <p class="email">lw_korvi@calmhaus.ca</p>
    <p class="address">5217 E Halden Row, Vancouver, BC V5N 4K7<br>korvi@calmhaus.ca</p>
  </div>
</div>
</body>
</html>
```